Dietitian needs awesome business card

I need a contemporary design that's eye catching but professional.
My card is to given to doctors, specialists and patients alike.
I manage patients with chronic diseases
I have uploaded my logo and current business card, I would also like the other Certified Clinical Nutritionist logo incorporated into the design

Target Market(s)

Doctors, specialists and patients

Industry/Entity Type

Healthcare

Contact Information for Business Card

www.brightfieldnutrition.com.au
Ph: 0427 561 903
Fax: 6457 2183
email: marcus.k.diet@fernmail.com
Space on the back of the card with: Appointment date, Appointment time and appointment location

Font styles to use
Serif

Colors
fbee3e
876aae
ffc214

Requirements
Must have
• My Logo
• Certified Clinical Nutritionist Logo
• My 4 locations - Pinebrook Medical Centre, North Corrin Health, Hollis Medical, Ashcombe Doctors Surgery
Nice to have
• I like the colours in my current business card

```html
<!DOCTYPE html>
<html lang="en">
<head>
<meta charset="utf-8">
<title>Brightfield Nutrition &amp; Dietetics – Business Card</title>
<link rel="stylesheet" href="https://fonts.googleapis.com/css2?family=Philosopher:wght@400;700&family=Open+Sans:wght@400;600&display=swap">
<style>
  :root {
    --backdrop: #8e8e8e;
    --navy: #1f2f8f;
    --royal: #0a7ccf;
    --deep: #1c2a86;
    --leaf: #7cc31f;
    --lime: #b4d82a;
    --white: #ffffff;
    --ink: #4a4a4a;
    --rule: #9a9a9a;
    --brand-blue: #2a3a9a;
    --badge: #f47a20;
  }
  * { box-sizing: border-box; margin: 0; padding: 0; }
  html, body { width: 1105px; height: 1200px; overflow: hidden; }
  body {
    position: relative;
    background: var(--backdrop);
    font-family: "Open Sans", Arial, sans-serif;
  }
  .card {
    position: absolute;
    left: 182px;
    width: 746px;
    height: 427px;
    overflow: hidden;
    background: var(--white);
  }
  .card--front { top: 119px; }
  .card--back { top: 637px; }

  /* Front */
  .front-field {
    position: absolute; left: 0; top: 0; width: 540px; height: 100%;
    background: radial-gradient(circle at 55% 40%, var(--royal) 0%, #1656b4 35%, var(--deep) 80%);
  }
  .front-emblem {
    position: absolute; left: 377px; top: 27px; width: 372px; height: 372px;
    border-radius: 50%;
    border: 4px solid var(--white);
    background: linear-gradient(160deg, #1650b0 0%, #4aa0d8 45%, var(--leaf) 75%, var(--lime) 100%);
  }
  .holder-name {
    position: absolute; left: 41px; top: 40px;
    font-family: "Philosopher", Georgia, serif;
    font-size: 26px; color: var(--white); letter-spacing: 0.3px;
  }
  .holder-role {
    position: absolute; left: 41px; top: 77px;
    font-family: "Philosopher", Georgia, serif;
    font-size: 19px; color: var(--white);
  }
  .contact-list {
    position: absolute; left: 41px; top: 276px; list-style: none;
  }
  .contact-list li {
    display: flex; align-items: center; gap: 9px;
    height: 28.6px;
    font-family: "Philosopher", Georgia, serif;
    font-size: 19px; color: var(--white);
  }
  .contact-list svg { width: 17px; height: 17px; flex: none; fill: var(--white); }

  /* Back */
  .brand {
    position: absolute; left: 48px; top: 40px;
    display: flex; align-items: center; gap: 12px;
  }
  .brand-dot { width: 58px; height: 58px; border-radius: 50%; background: var(--brand-blue); }
  .brand-name {
    font-family: "Philosopher", Georgia, serif;
    font-size: 25px; color: var(--brand-blue); line-height: 1.1; width: 230px;
  }
  .credential {
    position: absolute; left: 504px; top: 40px; width: 178px; height: 83px;
    background: var(--badge); border-radius: 3px;
    display: flex; align-items: center; justify-content: space-between;
    padding: 0 14px 0 9px;
  }
  .credential-text { font-size: 12.5px; line-height: 1.3; color: var(--white); }
  .credential-mark { width: 56px; height: 56px; border-radius: 50%; border: 3px solid var(--white); }
  .note-line {
    position: absolute; left: 50px; width: 644px; height: 0;
    border-top: 1.5px solid var(--rule);
  }
  .appointment {
    position: absolute; left: 50px; top: 272px; width: 650px;
    display: flex; align-items: flex-end;
    color: var(--brand-blue);
  }
  .appointment .label { font-size: 20px; margin-right: 8px; }
  .appointment .fill { border-bottom: 1.5px solid var(--rule); height: 22px; }
  .appointment .meridiem { font-size: 15px; margin-left: 6px; }
  .locations {
    position: absolute; left: 50px; top: 330px; width: 650px;
    display: grid; grid-template-columns: 378px 1fr; row-gap: 9px;
    list-style: none;
  }
  .locations li {
    display: flex; align-items: center; gap: 9px;
    font-size: 19px; color: var(--ink);
  }
  .locations .box { width: 16px; height: 16px; border: 2px solid var(--brand-blue); }
</style>
</head>
<body>
  <section class="card card--front">
    <div class="front-field"></div>
    <div class="front-emblem" role="img" aria-label="Practice emblem in blue and green tones"></div>
    <h1 class="holder-name">Marcus Kellaway</h1>
    <p class="holder-role">Nutritionist &amp; Chef</p>
    <ul class="contact-list">
      <li>
        <svg viewBox="0 0 24 24" aria-hidden="true"><path d="M6.6 10.8c1.4 2.8 3.8 5.1 6.6 6.6l2.2-2.2c.3-.3.7-.4 1-.2 1.1.4 2.3.6 3.6.6.6 0 1 .4 1 1V20c0 .6-.4 1-1 1C10.6 21 3 13.4 3 4c0-.6.4-1 1-1h3.5c.6 0 1 .4 1 1 0 1.3.2 2.5.6 3.6.1.3 0 .7-.2 1z"/></svg>
        0427 561 903
      </li>
      <li>
        <svg viewBox="0 0 24 24" aria-hidden="true"><path d="M6 3h10l2 2v4H6z M3 10h18v8h-3v3H6v-3H3z M8 15v4h8v-4z"/></svg>
        6457 2183
      </li>
      <li>
        <svg viewBox="0 0 24 24" aria-hidden="true"><path d="M2 5h20v14H2z M4 7v.5l8 5 8-5V7z"/></svg>
        marcus.k.diet@fernmail.com
      </li>
      <li>
        <svg viewBox="0 0 24 24" aria-hidden="true"><circle cx="12" cy="12" r="10"/><path d="M8 7c2 0 3 1 3 3s-2 2-2 4 1 3 1 5M15 5c-1 2 0 3 2 4" stroke="#1c2a86" stroke-width="1.6" fill="none"/></svg>
        brightfieldnutrition.com.au
      </li>
    </ul>
  </section>

  <section class="card card--back">
    <div class="brand">
      <span class="brand-dot"></span>
      <span class="brand-name">Brightfield Nutrition &amp; Dietetics</span>
    </div>
    <div class="credential">
      <span class="credential-text">Certified<br>Clinical<br>Nutritionist</span>
      <span class="credential-mark"></span>
    </div>

    <div class="note-line" style="top:167px"></div>
    <div class="note-line" style="top:206px"></div>
    <div class="note-line" style="top:247px"></div>

    <div class="appointment">
      <span class="label">Date :</span>
      <span class="fill" style="width:305px"></span>
      <span class="label" style="margin-left:10px">Time :</span>
      <span class="fill" style="width:143px"></span>
      <span class="meridiem">AM/PM</span>
    </div>

    <ul class="locations">
      <li><span class="box"></span>Pinebrook Medical Centre</li>
      <li><span class="box"></span>Ashcombe Doctors Surgery</li>
      <li><span class="box"></span>North Corrin Health</li>
      <li><span class="box"></span>Hollis Medical</li>
    </ul>
  </section>
</body>
</html>
```